Corvane Holdings , new business card design

investment firm with corporate clients . need double sided business card , vertical and horizontal options ,logo must be clear. prefer pantone colors only and sharp design. website also www.corvane.ae

Khalid Bin Tarrafi
Managing Director
Tel. +971 4 387 2940
Mobile +971 50 518 2403
khalid@corvane.ae
Q-Span Plaza, officw 18-B07, Warqa Gardens, Dubai

Contact Information for Business Card

Khalid Bin Tarrafi
Managing Director

Font styles to use
Serif

Colors

Designer to choose colors to be used in the design.

```html
<!DOCTYPE html>
<html lang="en">
<head>
<meta charset="utf-8">
<title>Corvane Holdings – Business Card</title>
<link href="https://fonts.googleapis.com/css2?family=Lato:wght@300;400;700&display=swap" rel="stylesheet">
<style>
  :root {
    --backdrop: #e7e8eb;
    --card: #ffffff;
    --navy: #0b2266;
    --steel: #4c76a1;
    --ink: #1d1d22;
    --muted: #3c3c44;
    --white: #ffffff;
  }
  * { margin: 0; padding: 0; box-sizing: border-box; }
  html, body {
    width: 1200px; height: 960px; overflow: hidden;
    background: var(--backdrop);
    font-family: "Lato", Arial, sans-serif;
  }
  .canvas { position: relative; width: 1200px; height: 960px; }
  .card {
    position: absolute; width: 600px; height: 340px;
    background: var(--card);
    box-shadow: 0 10px 28px rgba(0,0,0,.18);
    overflow: hidden;
  }
  .card--front { left: 130px; top: 110px; }
  .card--back { left: 470px; top: 500px; }

  .wordmark { display: flex; align-items: center; gap: 14px; color: var(--ink); font-weight: 300; }
  .wordmark__square { width: 14px; height: 14px; background: var(--steel); flex: none; }
  .wordmark__text { line-height: 1; text-transform: uppercase; }
  .wordmark__name { display: block; letter-spacing: .28em; }
  .wordmark__sub { display: block; letter-spacing: .62em; margin-top: 8px; }

  .card--front .wordmark { position: absolute; left: 0; right: 0; top: 108px; justify-content: center; }
  .card--front .wordmark__name { font-size: 54px; }
  .card--front .wordmark__sub { font-size: 16px; }
  .front__web {
    position: absolute; left: 0; right: 0; top: 238px; text-align: center;
    font-size: 20px; letter-spacing: .16em; color: var(--muted);
  }

  .card--back .wordmark { position: absolute; left: 34px; top: 44px; }
  .card--back .wordmark__name { font-size: 40px; }
  .card--back .wordmark__sub { font-size: 12px; margin-top: 6px; }

  .person { position: absolute; left: 46px; top: 150px; }
  .person__name { font-size: 16px; font-weight: 700; color: var(--navy); text-transform: uppercase; letter-spacing: .02em; }
  .person__role { font-size: 15px; color: var(--navy); text-transform: uppercase; margin-top: 4px; }

  .address { position: absolute; left: 46px; top: 232px; display: flex; gap: 10px; font-size: 14.5px; color: var(--muted); line-height: 1.3; }
  .address svg { margin-top: 6px; flex: none; }

  .accent-area { position: absolute; left: 0; top: 0; }

  .contacts {
    position: absolute; right: 22px; top: 210px; list-style: none;
    color: var(--white); font-size: 14.5px; text-align: right;
  }
  .contacts li { display: flex; justify-content: flex-end; align-items: center; gap: 7px; height: 24px; }
  .contacts svg { flex: none; }
</style>
</head>
<body>
<main class="canvas">

  <section class="card card--front" aria-label="Card front">
    <div class="wordmark">
      <span class="wordmark__square"></span>
      <span class="wordmark__text">
        <span class="wordmark__name">Corvane</span>
        <span class="wordmark__sub">Holdings</span>
      </span>
    </div>
    <p class="front__web">www.corvane.ae</p>
  </section>

  <section class="card card--back" aria-label="Card back">
    <svg class="accent-area" width="600" height="340" viewBox="0 0 600 340" role="img" aria-label="Decorative wave area in navy and steel blue">
      <path fill="var(--navy)" d="M60,340 C260,336 380,270 440,190 C490,130 550,112 600,110 L600,340 Z"/>
    </svg>

    <div class="wordmark">
      <span class="wordmark__square"></span>
      <span class="wordmark__text">
        <span class="wordmark__name">Corvane</span>
        <span class="wordmark__sub">Holdings</span>
      </span>
    </div>

    <div class="person">
      <p class="person__name">Khalid Bin Tarrafi</p>
      <p class="person__role">Managing Director</p>
    </div>

    <p class="address">
      <svg width="12" height="16" viewBox="0 0 12 16" aria-hidden="true"><path fill="var(--navy)" d="M6 0a6 6 0 0 0-6 6c0 4.5 6 10 6 10s6-5.5 6-10a6 6 0 0 0-6-6zm0 8.5A2.5 2.5 0 1 1 6 3.5a2.5 2.5 0 0 1 0 5z"/></svg>
      <span>Q-Span Plaza, officw 18-B07<br>Warqa Gardens, Dubai</span>
    </p>

    <ul class="contacts">
      <li>
        <svg width="13" height="13" viewBox="0 0 16 16" aria-hidden="true"><circle cx="8" cy="8" r="7" fill="none" stroke="currentColor" stroke-width="1.4"/><path fill="currentColor" d="M5.5 4.5l1.3-.3.8 1.8-.9.7c.4.9 1 1.5 1.9 1.9l.7-.9 1.8.8-.3 1.3c-3 .3-5.6-2.3-5.3-5.3z"/></svg>
        +971 4 387 2940
      </li>
      <li>
        <svg width="10" height="14" viewBox="0 0 10 14" aria-hidden="true"><rect x="1" y="0.5" width="8" height="13" rx="1.5" fill="none" stroke="currentColor" stroke-width="1.3"/><circle cx="5" cy="11" r="1" fill="currentColor"/></svg>
        +971 50 518 2403
      </li>
      <li>
        <svg width="14" height="11" viewBox="0 0 14 11" aria-hidden="true"><rect x="0.6" y="0.6" width="12.8" height="9.8" fill="none" stroke="currentColor" stroke-width="1.2"/><path d="M1 1l6 5 6-5" fill="none" stroke="currentColor" stroke-width="1.2"/></svg>
        khalid@corvane.ae
      </li>
      <li>
        <svg width="13" height="13" viewBox="0 0 16 16" aria-hidden="true"><g fill="none" stroke="currentColor" stroke-width="1.3"><circle cx="8" cy="8" r="7"/><ellipse cx="8" cy="8" rx="3" ry="7"/><path d="M1 8h14"/></g></svg>
        www.corvane.ae
      </li>
    </ul>
  </section>

</main>
</body>
</html>
```